Assessment Report cover design and formatting

This report is for senior executives and provides leaders with detailed insight into their capabilities and skills. The cover should have space for the date and name of the person doing the assessment. We are looking to modernise the report cover design. We would like the report to be our company colours if possible. The work will likely expand once the cover is done to other parts of the report, ie. the format and layout of the report etc.

Company colours:
Primary colours:
• Blue #0D47A1, #115CD0, #90B6ED, #EEf3FB
• Green #0D91A1, #47A10D, #324C196, #0DA11D
Additional colours:
• Purple #A10D91
• Brown #A1670D
• Red #A10D47

Target Market(s)

Executives

Industry/Entity Type

Consulting, leadership development

Colors
0094D4
00A9DD
6FCCEA
C7EBF8
E9F6FB
00AB8E
00BBA5
67D7C9
C6EFE9
E9F9F6
E54698
E96AAD
F1A4CE
F9D9EA
FCEFF6
6B429C
8869AF
B7A5CE
E3DAEB
F3F0F8

Requirements
Must have
• The report cover should have space for name of user, the date and company logo. Cover should be in A4 size.

```html
<!DOCTYPE html>
<html lang="en">
<head>
<meta charset="UTF-8">
<title>Growth Leader Assessment – Insight Report</title>
<link href="https://fonts.googleapis.com/css2?family=Libre+Franklin:wght@600;700&family=Arimo:wght@400;700&display=swap" rel="stylesheet">
<style>
  :root {
    --page: #ffffff;
    --ink: #111111;
    --indigo: #3c3f96;
    --brand-blue: #0d6fd0;
    --brand-navy: #1f3f96;
    --ring-light: #a6dcf6;
    --ring-mid: #3f9de6;
    --ring-deep: #1673d6;
    --white: #ffffff;
  }
  * { margin: 0; padding: 0; box-sizing: border-box; }
  html, body {
    width: 927px;
    height: 1200px;
    overflow: hidden;
    background: var(--page);
  }
  .cover {
    position: relative;
    width: 927px;
    height: 1200px;
    background: var(--page);
    font-family: "Arimo", Arial, sans-serif;
    color: var(--ink);
  }
  .hero {
    position: absolute;
    left: 60px;
    top: 0;
    width: 807px;
    height: 877px;
    background:
      radial-gradient(ellipse 62% 58% at 47% 45%, var(--ring-light) 0%, #7cc4f0 22%, var(--ring-mid) 55%, var(--ring-deep) 100%);
  }
  .title {
    position: absolute;
    left: 139px;
    top: 712px;
    color: var(--white);
    font-family: "Libre Franklin", Arial, sans-serif;
  }
  .title__main {
    font-weight: 700;
    font-size: 50px;
    line-height: 1;
    letter-spacing: -0.5px;
  }
  .title__sub {
    display: flex;
    align-items: center;
    gap: 12px;
    margin-top: 6px;
    font-weight: 600;
    font-size: 24px;
    line-height: 1;
  }
  .title__rule {
    display: block;
    width: 243px;
    height: 3px;
    background: var(--white);
    margin-top: 12px;
  }
  .recipient {
    position: absolute;
    left: 139px;
    top: 954px;
    width: 260px;
  }
  .recipient__bar {
    width: 118px;
    height: 8px;
    background: var(--indigo);
  }
  .recipient__label {
    margin-top: 26px;
    font-size: 18px;
    letter-spacing: -0.2px;
  }
  .recipient__name {
    margin-top: 4px;
    font-size: 40px;
    font-weight: 700;
    color: var(--brand-blue);
    line-height: 1.1;
  }
  .recipient__date {
    margin-top: 4px;
    font-size: 19px;
  }
  .recipient__bar--bottom {
    margin-top: 26px;
  }
  .company {
    position: absolute;
    right: 60px;
    top: 985px;
    display: flex;
    align-items: center;
    gap: 14px;
    color: var(--brand-navy);
    font-family: "Arimo", Arial, sans-serif;
    font-weight: 400;
    font-size: 36px;
    line-height: 1.15;
    text-align: right;
  }
  .company__dot {
    width: 22px;
    height: 22px;
    border-radius: 50%;
    background: #2a9d8f;
    flex: none;
  }
  .confidential {
    position: absolute;
    left: 0;
    right: 0;
    top: 1160px;
    text-align: center;
    font-size: 14px;
    font-weight: 700;
    letter-spacing: 4px;
    color: var(--brand-blue);
  }
</style>
</head>
<body>
  <main class="cover">
    <div class="hero" role="img" aria-label="Abstract blue tree-ring texture radiating from a light centre"></div>

    <header class="title">
      <h1 class="title__main">GROWTH LEADER</h1>
      <p class="title__sub">ASSESSMENT <span class="title__rule"></span></p>
    </header>

    <section class="recipient">
      <div class="recipient__bar"></div>
      <p class="recipient__label">INSIGHT REPORT FOR:</p>
      <p class="recipient__name">Sample</p>
      <p class="recipient__date">00 Month 2023</p>
      <div class="recipient__bar recipient__bar--bottom"></div>
    </section>

    <div class="company">
      <span class="company__dot"></span>
      <span class="company__name">Meridian<br>Advisory</span>
    </div>

    <p class="confidential">CONFIDENTIAL</p>
  </main>
</body>
</html>
```